Updated DJ business Card showing other businesses

DJ Talbo offers professional mobile dj services including DJ. MC. Karaoke.
Silent Disco (will attach logo)
I also offer a 360 Photo Booth.

Contact info:
(405) 555-0147
mark.fenstell@pelimail.com
Social Media @DJTalboOKC

```html
<!DOCTYPE html>
<html lang="en">
<head>
<meta charset="utf-8">
<title>DJ Talbo Business Card</title>
<link rel="stylesheet" href="https://fonts.googleapis.com/css2?family=Fredoka:wght@500;600;700&family=Montserrat:wght@400;500&display=swap">
<style>
  :root {
    --stage: #3b3b3d;
    --crimson: #d3234a;
    --white: #ffffff;
    --ink: #141414;
    --yellow: #f2ee1e;
    --violet: #5a2a7a;
    --magenta: #b0307e;
    --night: #1c1633;
  }
  * { box-sizing: border-box; margin: 0; padding: 0; }
  html, body {
    width: 1200px; height: 689px; overflow: hidden;
    background: var(--stage);
  }
  .sheet {
    position: relative; width: 1200px; height: 689px;
    display: flex; align-items: center; justify-content: center; gap: 40px;
  }
  .card {
    position: relative; width: 540px; height: 310px; overflow: hidden;
    box-shadow: 0 14px 30px rgba(0,0,0,.45);
  }
  /* Front */
  .card--front {
    background: var(--crimson);
    display: flex; align-items: center; justify-content: center;
  }
  .brand {
    display: flex; align-items: center; gap: 16px;
    font-family: "Fredoka", sans-serif; font-weight: 700;
    color: var(--white); text-transform: uppercase;
  }
  .brand__dot { border-radius: 50%; background: var(--ink); flex: none; }
  .card--front .brand { font-size: 58px; letter-spacing: 1px; }
  .card--front .brand__dot { width: 70px; height: 70px; }

  /* Back */
  .card--back { background: var(--night); }
  .card__photo {
    position: absolute; inset: 0;
    background:
      linear-gradient(160deg, rgba(0,0,0,0) 55%, var(--yellow) 78%),
      radial-gradient(circle at 25% 60%, #c9486a 0%, rgba(0,0,0,0) 40%),
      linear-gradient(120deg, var(--night) 0%, var(--violet) 45%, var(--magenta) 80%);
  }
  .card__content {
    position: absolute; inset: 0; padding: 26px 30px;
    display: flex; flex-direction: column; align-items: center;
    font-family: "Fredoka", sans-serif;
  }
  .card__name {
    font-size: 50px; font-weight: 700; color: var(--white); line-height: 1;
  }
  .card__tagline {
    margin-top: 10px; font-size: 17px; font-weight: 600; color: var(--yellow);
  }
  .card__services {
    margin-top: 6px; font-size: 30px; font-weight: 600; color: var(--white);
  }
  .card__offer {
    margin-top: 10px; padding: 6px 26px; border-radius: 30px;
    background: var(--crimson); color: var(--white);
    font-size: 22px; font-weight: 600;
  }
  .card__footer {
    position: absolute; left: 30px; right: 26px; bottom: 20px;
    display: flex; justify-content: space-between; align-items: flex-end;
  }
  .card--back .brand { font-size: 24px; color: var(--ink); gap: 8px; }
  .card--back .brand__dot { width: 30px; height: 30px; }
  .contact {
    list-style: none; font-family: "Montserrat", sans-serif;
    font-size: 12.5px; color: var(--ink); line-height: 1.55;
  }
  .contact li { display: flex; align-items: center; gap: 6px; }
  .contact svg { width: 12px; height: 12px; fill: var(--ink); }
</style>
</head>
<body>
<main class="sheet">
  <section class="card card--front">
    <div class="brand"><span class="brand__dot"></span><span>Silent Disco</span></div>
  </section>

  <section class="card card--back">
    <div class="card__photo" role="img" aria-label="Blurred photo of a DJ's hands on a mixing deck under purple club lights"></div>
    <div class="card__content">
      <h1 class="card__name">DJ Talbo</h1>
      <p class="card__tagline">offers professional Mobile Dj Services including</p>
      <p class="card__services">DJ. MC. Karaoke</p>
      <p class="card__offer">I also offer a 360 Photo Booth.</p>
    </div>
    <div class="card__footer">
      <div class="brand"><span class="brand__dot"></span><span>Silent Disco</span></div>
      <ul class="contact">
        <li><svg viewBox="0 0 24 24"><path d="M6.6 10.8a15 15 0 0 0 6.6 6.6l2.2-2.2a1 1 0 0 1 1-.25 11.4 11.4 0 0 0 3.6.57 1 1 0 0 1 1 1V20a1 1 0 0 1-1 1A17 17 0 0 1 3 4a1 1 0 0 1 1-1h3.5a1 1 0 0 1 1 1c0 1.25.2 2.45.57 3.57a1 1 0 0 1-.25 1z"/></svg>(405) 555-0147</li>
        <li><svg viewBox="0 0 24 24"><path d="M2 5h20v14H2z M2 5l10 8 10-8" /></svg>mark.fenstell@pelimail.com</li>
        <li>Social Media @DJTalboOKC</li>
      </ul>
    </div>
  </section>
</main>
</body>
</html>
```